Musician looking for catchy Web Design for promotion

My name is Brenna Coyle. I'm an Irish musician who plays the tin whistle and the flute. I'm also the leader of a traditional Irish music and dance ensemble called Gather the Willows (www.gatherthewillows-example.com) and for the past 30 years, I've toured the world performing thousands of concerts. I run an annual cruise (www.brennacoylevoyage-example.com) that I would like a link to, and I'm also I'm organizing tours to Ireland that I would like a page set up for. I'm looking for a website to promote my tours and my music.
Updates

Hello Graphic Designers, I am only looking for the design of the home page to make my decision. Thank you. Brenna

Target Market(s)

Music fans of Irlsh and World Music

Industry/Entity Type

Entertainment Industry

Number of Pages Required

5+ page

Requirements
Must have
• I'm looking for a catchy design that shows a photo of me. I would like a few links....
• BIO
• TOURDATES
• BRENNA COYLE CRUISE
• MUSICAL TOUR OF IRELAND
• CONTACT
• VIDEO
• GALLERY
• CONTACT
• MAILING LIST
• STORE
Nice to have
• we'll see!

```html
<!DOCTYPE html>
<html lang="en">
<head>
<meta charset="utf-8">
<title>Brenna Coyle — Musical Tour of Ireland</title>
<link rel="stylesheet" href="https://fonts.googleapis.com/css2?family=Roboto:wght@400;500;700;900&family=Open+Sans:wght@400;600;700&display=swap">
<style>
:root{
  --ink:#1c1c1c;
  --text:#555;
  --muted:#8a8a8a;
  --white:#fff;
  --panel:#262626;
  --band:#cfdde3;
  --footer:#1f1f1f;
  --footer-base:#141414;
  --accent:#e0b23a;
  --line:#e3e3e3;
}
*{box-sizing:border-box;margin:0;padding:0}
html,body{width:1200px;height:3327px;overflow:hidden;background:var(--white)}
body{font-family:"Open Sans",Arial,sans-serif;color:var(--text);position:relative}
.abs{position:absolute}
.photo{position:absolute;display:block}

/* header */
.hero{left:0;top:0;width:1200px;height:787px;background:linear-gradient(180deg,#c9d3d9 0%,#8b9a8a 35%,#556b4e 60%,#4a5d52 80%,#5d7078 100%)}
.hero-sea{left:600px;top:160px;width:600px;height:627px;background:linear-gradient(180deg,#7f9aa8 0%,#5f7f8e 40%,#8a8c86 75%,#6e7466 100%)}
.hero-person{left:80px;top:120px;width:560px;height:667px;background:radial-gradient(ellipse at 50% 45%,#6f7a6c 0%,#4d5a4f 55%,rgba(77,90,79,0) 75%)}
.header{left:0;top:0;width:1200px;height:112px;background:linear-gradient(180deg,rgba(255,255,255,.92),rgba(255,255,255,.7))}
.header-rule{left:98px;top:112px;width:740px;height:5px;background:var(--ink)}
.brand{left:108px;top:44px;display:flex;align-items:center;gap:10px}
.brand-mark{width:30px;height:30px;background:var(--ink)}
.brand-name{font-family:"Roboto",sans-serif;font-weight:700;font-size:14px;color:var(--ink);line-height:1.15;letter-spacing:.5px}
.search{left:783px;top:18px;width:173px;height:26px;border:2px solid #3b4a53;border-radius:7px;font-size:11px;padding:4px 10px;color:#555}
.cart{left:994px;top:24px;font-family:"Roboto",sans-serif;font-weight:700;font-size:11px;color:var(--ink)}
.nav{left:350px;top:64px;display:flex;gap:13px;font-family:"Roboto",sans-serif;font-weight:500;font-size:10.5px;color:var(--ink);letter-spacing:.2px}
.hero-arrow{top:398px}
.hero-caption{left:100px;top:632px;width:854px;height:100px;background:rgba(30,30,30,.55);padding:12px 12px}
.hero-caption h1{font-family:"Roboto",sans-serif;font-size:34px;color:var(--white);font-weight:700;letter-spacing:.5px}
.hero-caption h1 span{font-weight:400}
.hero-caption p{font-size:10px;font-weight:700;color:var(--white);text-transform:uppercase;line-height:1.5;margin-top:4px;letter-spacing:.3px}

/* section titles */
.section-title{left:0;width:1200px;text-align:center;font-family:"Roboto",sans-serif;font-weight:700;font-size:36px;color:var(--ink);letter-spacing:1px}
.title-bar{left:585px;width:30px;height:3px;background:var(--ink)}
.date{left:0;width:1200px;text-align:center;font-size:10px;color:var(--muted);letter-spacing:1px}

/* about */
.about{left:98px;top:916px;width:1004px;height:388px;border:1px solid #111}
.about-text{left:98px;top:916px;width:623px;height:388px;background:var(--panel);padding:42px 58px 0}
.about-text h3{font-family:"Roboto",sans-serif;font-size:22px;color:var(--white);font-weight:700;margin-bottom:18px}
.about-text h3 span{font-weight:400}
.about-text p{font-size:11.5px;line-height:1.55;color:var(--white);margin-bottom:14px}
.about-text p.dim{color:#5d5d5d}
.about-photo{left:721px;top:916px;width:381px;height:388px;background:radial-gradient(ellipse at 50% 60%,#3a2f28 0%,#6e5530 55%,#a98745 100%)}

.lead{left:150px;width:900px;text-align:center;font-size:11.5px;line-height:1.6;color:var(--text)}
.thumb{top:1455px;width:171px;height:135px}

/* tour band */
.band{left:0;top:1652px;width:1200px;height:378px;background:var(--band)}
.tour-card{top:1743px;height:242px}
.card-label{left:0;bottom:0;width:100%;height:46px;background:rgba(20,20,20,.65);color:var(--white);text-align:center;padding-top:6px}
.card-label b{display:block;font-family:"Roboto",sans-serif;font-size:13px;letter-spacing:.5px}
.card-label span{font-size:12px}

/* gallery */
.view-icons{left:560px;top:2112px;display:flex;gap:8px}
.tile{height:204px}
.tile .card-label{height:48px}
.tile .card-label span{font-size:11px;line-height:1.3;display:block}

/* news + testimonials */
.col-head{font-family:"Roboto",sans-serif;font-weight:700;font-size:19px;color:var(--ink)}
.col-rule{height:1px;background:var(--line)}
.col-rule-strong{height:2px;background:var(--ink)}
.news-img{width:113px;height:113px}
.news-title{font-family:"Roboto",sans-serif;font-weight:700;font-size:17px;color:var(--ink)}
.news-meta{font-size:9px;color:var(--muted)}
.news-body{font-size:10.5px;line-height:1.55;color:var(--muted);width:360px}
.quote-box{left:621px;top:2733px;width:481px;height:161px;border:1px solid var(--line);padding:34px 40px 0 85px;font-size:12px;line-height:1.65;color:var(--muted)}
.quote-mark{width:26px;height:26px;background:var(--ink);color:var(--white);font-family:"Roboto",sans-serif;font-weight:900;font-size:24px;line-height:32px;text-align:center}
.avatar{left:621px;top:2917px;width:48px;height:48px;background:#cfcfcf}
.author{left:695px;top:2922px;font-size:13px;color:var(--ink)}
.author small{display:block;font-size:10px;color:var(--text)}
.pager{top:2652px;width:20px;height:20px;border:1px solid #ccc;background:#f3f3f3}

/* footer */
.footer{left:0;top:3008px;width:1200px;height:270px;background:var(--footer)}
.footer-col{top:3070px;color:var(--white);font-size:10.5px;line-height:1.6}
.footer-col h4{font-family:"Roboto",sans-serif;font-size:13px;font-weight:700;margin-bottom:20px;letter-spacing:.3px}
.contact-row{display:flex;gap:16px;align-items:flex-start;margin-bottom:10px}
.contact-row svg{flex:none;margin-top:2px}
.social{display:flex;gap:16px;margin-bottom:30px}
.social span{width:16px;height:16px;border-radius:50%;background:#8c8c8c;display:block}
.social span.on{background:var(--accent)}
.signup{display:flex;width:262px;height:34px;background:var(--white);align-items:center;justify-content:space-between;padding:0 12px;font-size:9.5px;color:#999;letter-spacing:.4px;margin-top:12px}
.to-top{left:1057px;top:3034px;width:40px;height:40px;border-radius:50%;border:2px solid #555}
.base{left:0;top:3278px;width:1200px;height:49px;background:var(--footer-base);color:var(--white);font-size:9.5px}
</style>
</head>
<body>

<!-- hero -->
<div class="abs hero"></div>
<div class="photo hero-sea" role="img" aria-label="Rocky Irish coastline with sea and green headland"></div>
<div class="photo hero-person" role="img" aria-label="Brenna Coyle smiling, holding a tin whistle on the coast"></div>

<header>
  <div class="abs header"></div>
  <div class="abs brand"><span class="brand-mark"></span><span class="brand-name">BRENNA COYLE'S<br>MUSICAL TOUR OF IRELAND</span></div>
  <div class="abs search">search...</div>
  <div class="abs cart">SHOPPING CART (0)</div>
  <nav class="abs nav">
    <span>BIO</span><span>TOURDATES</span><span>BRENNA COYLE CRUISE</span><span>MUSICAL TOUR OF IRELAND</span><span>CONTACT</span><span>VIDEO</span><span>GALLERY</span><span>CONTACT</span><span>MAILING LIST</span><span>STORE</span>
  </nav>
  <div class="abs header-rule"></div>
</header>

<svg class="abs hero-arrow" style="left:96px" width="24" height="34" viewBox="0 0 24 34"><path d="M20 2 L4 17 L20 32" fill="none" stroke="#fff" stroke-width="2.5"/></svg>
<svg class="abs hero-arrow" style="left:1068px" width="24" height="34" viewBox="0 0 24 34"><path d="M4 2 L20 17 L4 32" fill="none" stroke="#fff" stroke-width="2.5"/></svg>

<div class="abs hero-caption">
  <h1>LOREM <span>IPSUM</span></h1>
  <p>It is a long established fact that a reader will be distracted by the readable content of a page when looking at its layout. The point of using<br>Lorem Ipsum is that it has a more-or-less normal distribution of letters, as opposed to using 'Content here.</p>
</div>

<!-- about -->
<h2 class="abs section-title" style="top:815px">ABOUT US</h2>
<div class="abs title-bar" style="top:864px"></div>
<div class="abs date" style="top:873px">JULY 10, 2016</div>

<div class="abs about-text">
  <h3>LOREM <span>IPSUM</span></h3>
  <p>It is a long established fact that a reader will be distracted by the readable content of a page when looking at its layout. The point of using Lorem Ipsum is that it has a more-or-less normal distribution of letters, as opposed to using 'Content here,</p>
  <p class="dim" style="margin-top:34px">There are many variations of passages of Lorem Ipsum available, but the majority have suffered alteration in some form, by injected humour, or randomised words which don't look even slightly believable.</p>
  <p class="dim">It uses a dictionary of over 200 Latin words, combined with a handful of model sentence structures, to generate Lorem Ipsum which looks reasonable. The generated Lorem Ipsum is therefore always free from repetition, injected humour, or non-characteristic words etc.</p>
</div>
<div class="photo about-photo" role="img" aria-label="Portrait of Brenna Coyle holding a flute"></div>
<div class="abs about"></div>

<!-- cruise -->
<h2 class="abs section-title" style="top:1334px">BRENNA COYLE CRUISE</h2>
<div class="abs title-bar" style="top:1382px"></div>
<p class="abs lead" style="top:1400px">It is a long established fact that a reader will be distracted by the readable content of a page when looking at its layout. The point of using Lorem Ipsum is that it has a more-or-less normal distribution of letters, as opposed to using 'Content here,</p>
<div class="photo thumb" style="left:98px;background:linear-gradient(180deg,#9cc3e6,#dfe8ef 55%,#2f5f86 70%,#204a6e)" role="img" aria-label="Cruise ship at sea"></div>
<div class="photo thumb" style="left:306px;background:linear-gradient(180deg,#7fb4e2,#c94b3c 50%,#9a2c22 80%,#6a5a4c)" role="img" aria-label="Cruise ship deck with red sun loungers"></div>
<div class="photo thumb" style="left:515px;background:linear-gradient(180deg,#6aaee0,#e8eef2 45%,#48b8c8 70%,#d9d2b5)" role="img" aria-label="Cruise ship pool deck"></div>
<div class="photo thumb" style="left:723px;background:linear-gradient(180deg,#3a78c4,#8ab0dc 45%,#6e7c68 70%,#4a5445)" role="img" aria-label="Lighthouse on a rocky shore"></div>
<div class="photo thumb" style="left:932px;background:linear-gradient(180deg,#2f67b8,#9ab8d8 50%,#b9b4a8 70%,#2a4f72)" role="img" aria-label="Harbour city skyline"></div>
<p class="abs lead" style="top:1604px">It is a long established fact that a reader will be distracted by the readable content of a page when looking at its layout.</p>

<!-- musical tour -->
<div class="abs band"></div>
<h2 class="abs section-title" style="top:1675px">MUSICAL TOUR OF IRELAND</h2>
<div class="abs title-bar" style="top:1722px"></div>
<div class="photo tour-card" style="left:98px;width:377px;background:radial-gradient(ellipse at 45% 45%,#3b3128,#6d6048 50%,#9b8a66)" role="img" aria-label="Brenna Coyle in front of an ornate iron gate">
  <div class="abs card-label"><b>LOREM IPSUM</b><span>There are many variations of passages</span></div>
</div>
<div class="photo tour-card" style="left:484px;width:618px;background:linear-gradient(180deg,#7ea8d6,#b9cfe6 25%,#3b6a4c 45%,#1f5a8c 60%,#1b4f7e)" role="img" aria-label="Cruise ship off a coastal town">
  <div class="abs card-label"><b>LOREM IPSUM</b><span>There are many variations of passages of Lorem Ipsum available,</span></div>
</div>

<!-- gallery -->
<h2 class="abs section-title" style="top:2044px;font-weight:500;font-size:30px">GALLERY</h2>
<svg class="abs view-icons" width="80" height="12" viewBox="0 0 80 12">
  <g fill="#888"><rect x="0" y="1" width="12" height="2"/><rect x="0" y="5" width="12" height="2"/><rect x="0" y="9" width="12" height="2"/></g>
  <g fill="#333"><rect x="22" y="1" width="3" height="3"/><rect x="27" y="1" width="3" height="3"/><rect x="32" y="1" width="3" height="3"/><rect x="22" y="7" width="3" height="3"/><rect x="27" y="7" width="3" height="3"/><rect x="32" y="7" width="3" height="3"/></g>
  <g fill="#888"><rect x="45" y="1" width="4" height="4"/><rect x="51" y="1" width="4" height="4"/><rect x="45" y="7" width="4" height="4"/><rect x="51" y="7" width="4" height="4"/></g>
  <g fill="#888"><rect x="66" y="1" width="2" height="2"/><rect x="70" y="1" width="10" height="2"/><rect x="66" y="5" width="2" height="2"/><rect x="70" y="5" width="10" height="2"/><rect x="66" y="9" width="2" height="2"/><rect x="70" y="9" width="10" height="2"/></g>
</svg>

<div class="photo tile" style="left:98px;top:2147px;width:496px;background:linear-gradient(180deg,#8cb6e0,#dce6ee 35%,#5b8a3e 55%,#6c8a90 75%,#4e6a44)" role="img" aria-label="Harbour fort with green lawns and boats">
  <div class="abs card-label"><b>LOREM IPSUM</b><span>There are many variations of passages of Lorem Ipsum available,</span></div>
</div>
<div class="photo tile" style="left:599px;top:2147px;width:248px;background:linear-gradient(180deg,#4a6fa0,#a86a48 40%,#7a4a32 60%,#3d566c)" role="img" aria-label="Colourful waterfront town at dusk">
  <div class="abs card-label"><span>you need to be sure there isn't anything embarrassing hidden</span></div>
</div>
<div class="photo tile" style="left:852px;top:2147px;width:250px;background:linear-gradient(180deg,#2c3a48,#6a7d8c 35%,#e8ecef 55%,#2d5b78 75%)" role="img" aria-label="Passenger ferry on the water">
  <div class="abs card-label"><span>you need to be sure there isn't anything embarrassing hidden</span></div>
</div>
<div class="photo tile" style="left:98px;top:2358px;width:246px;background:linear-gradient(180deg,#6fa6dc,#cfe0ee 35%,#4c7a56 50%,#2367a6 65%,#1c5a94)" role="img" aria-label="Cruise ship near an island town">
  <div class="abs card-label"><span>you need to be sure there isn't anything embarrassing hidden</span></div>
</div>
<div class="photo tile" style="left:348px;top:2358px;width:246px;background:linear-gradient(180deg,#e6eaee,#c8ccc8 35%,#8a7a5c 55%,#5c6e3c 80%)" role="img" aria-label="Church spire above a town square">
  <div class="abs card-label"><span>you need to be sure there isn't anything embarrassing hidden</span></div>
</div>
<div class="photo tile" style="left:599px;top:2358px;width:503px;background:linear-gradient(180deg,#7a8a96,#c3cbd0 30%,#4c6a3a 50%,#3c5a66 70%,#2b4656)" role="img" aria-label="Sea cliffs along the Irish coast">
  <div class="abs card-label"><b>LOREM IPSUM</b><span>There are many variations of passages of Lorem Ipsum available,</span></div>
</div>
<p class="abs lead" style="top:2574px;left:180px;width:840px">you need to be sure there isn't anything embarrassing hidden in the middle of text. All the Lorem Ipsum generators on the Internet tend to repeat predefined chunks as necessary, making this the first true generator on the Internet.</p>

<!-- latest news -->
<h3 class="abs col-head" style="left:98px;top:2650px">Latest News</h3>
<div class="abs col-rule" style="left:98px;top:2686px;width:480px"></div>
<div class="abs col-rule-strong" style="left:98px;top:2685px;width:112px"></div>

<div class="photo news-img" style="left:98px;top:2733px;background:radial-gradient(circle at 50% 50%,#b07a58,#6a3c22 60%,#3a2418)" role="img" aria-label="Hands playing a tin whistle"></div>
<h4 class="abs news-title" style="left:237px;top:2737px">Place Your Heading</h4>
<p class="abs news-meta" style="left:237px;top:2764px">September 15, 2016 &nbsp; Comments (4)</p>
<p class="abs news-body" style="left:237px;top:2788px">Cum sociis natoque penatibus et magnis dis parturient montesmus. Pro vel nibh et elit mollis commodo et nec augueique Mauris at justo eu lectus auctor porta vel ut libero.</p>

<div class="photo news-img" style="left:98px;top:2861px;background:linear-gradient(180deg,#e8ecef,#d8dbcf 40%,#c9a236 60%,#6b6a5a)" role="img" aria-label="Songbird perched on a branch"></div>
<h4 class="abs news-title" style="left:237px;top:2865px">Place Your Heading</h4>
<p class="abs news-meta" style="left:237px;top:2892px">September 15, 2016 &nbsp; Comments (4)</p>
<p class="abs news-body" style="left:237px;top:2916px">Cum sociis natoque penatibus et magnis dis parturient montesmus. Pro vel nibh et elit mollis commodo et nec augueique Mauris at justo eu lectus auctor porta vel ut libero.</p>

<!-- testimonials -->
<h3 class="abs col-head" style="left:621px;top:2650px">Testimonials</h3>
<div class="abs col-rule" style="left:621px;top:2686px;width:481px"></div>
<div class="abs col-rule-strong" style="left:621px;top:2685px;width:108px"></div>
<svg class="abs pager" style="left:1058px" viewBox="0 0 20 20"><path d="M12 6 L8 10 L12 14" fill="none" stroke="#999" stroke-width="1.5"/></svg>
<svg class="abs pager" style="left:1080px" viewBox="0 0 20 20"><path d="M8 6 L12 10 L8 14" fill="none" stroke="#999" stroke-width="1.5"/></svg>

<div class="abs quote-box">Cum sociis natoque penatibus et magnis dis parturient eimus. Pro vel nibh et elit mollis commodo et nec augueque Mauris at justo eu lectus auctor porta vel ut libero. Suspe mattis tellus vel augue mollis ultrices. Suspendisse poten.</div>
<div class="abs quote-mark" style="left:638px;top:2749px">“</div>
<div class="abs quote-mark" style="left:896px;top:2848px">”</div>
<svg class="abs" style="left:640px;top:2893px" width="20" height="11" viewBox="0 0 20 11"><path d="M0 0 L10 10 L20 0" fill="#fff" stroke="#e3e3e3"/></svg>
<div class="abs avatar" role="img" aria-label="Profile placeholder"></div>
<div class="abs author">Nora Whelan<small>Our Psychologist</small></div>

<!-- footer -->
<footer>
  <div class="abs footer"></div>
  <div class="abs to-top"><svg width="36" height="36" viewBox="0 0 36 36"><path d="M12 21 L18 15 L24 21" fill="none" stroke="#888" stroke-width="2"/></svg></div>

  <div class="abs footer-col" style="left:137px;width:250px">
    <h4>ABOUT US</h4>
    <p>Lorem ipsum dolor sit amet elit, consectetur adipiscing. Vestibulum luctus ipsum id quam euismod a malesuada sapien euismod.</p>
    <p style="margin-top:16px">If you have any difficulty, just copy the address into the "to" area and/or address book of your e-mail program and work away.</p>
  </div>

  <div class="abs footer-col" style="left:466px;width:260px">
    <h4>CONTACT INFORMATION</h4>
    <div class="contact-row">
      <svg width="14" height="12" viewBox="0 0 14 12"><path d="M7 0 L14 6 H12 V12 H8.5 V8 H5.5 V12 H2 V6 H0 Z" fill="#fff"/></svg>
      <div>Company Name<br>Address 1<br>Address 2<br>Town<br>Zip Code</div>
    </div>
    <div class="contact-row" style="margin-top:14px">
      <svg width="14" height="14" viewBox="0 0 14 14"><path d="M3 0 L5.5 3.5 L4 5 C5 7.5 6.5 9 9 10 L10.5 8.5 L14 11 L12 14 C5.5 13.5 .5 8.5 0 2 Z" fill="#fff"/></svg>
      <div>+1 555-010-7144</div>
    </div>
    <div class="contact-row" style="margin-top:14px">
      <svg width="14" height="11" viewBox="0 0 14 11"><rect x="0" y="0" width="14" height="11" fill="#fff"/><path d="M0 0 L7 6 L14 0" fill="none" stroke="#1f1f1f" stroke-width="1.2"/></svg>
      <div style="color:var(--accent)">pr@gatherthewillows-example.com</div>
    </div>
  </div>

  <div class="abs footer-col" style="left:794px;width:300px">
    <h4>CONNECT WITH US</h4>
    <div class="social"><span></span><span class="on"></span><span></span><span></span><span></span><span></span></div>
    <p>Sign up to our newsletter:</p>
    <div class="signup"><span>ENTER YOUR EMAIL ADDRESS HERE</span>
      <svg width="14" height="11" viewBox="0 0 14 11"><rect x="0" y="0" width="14" height="11" fill="#888"/><path d="M0 0 L7 6 L14 0" fill="none" stroke="#fff" stroke-width="1.2"/></svg>
    </div>
  </div>

  <div class="abs base">
    <span class="abs" style="left:98px;top:18px">Copyright © 2016</span>
    <span class="abs" style="left:982px;top:18px">Powered By Northgate Studio</span>
  </div>
</footer>

</body>
</html>
```